Walk Beside The River

Business Card design

Target Market(s)

People who require support in the commnity

Industry/Entity Type

Mental Health Support

Contact Information for Business Card

Mental Health Support Rosalind Tavener walkbesidetheriver@mailcove.com.au 0481 637 092 PO Box 926 Kelvale QLD 4571

Colors
6B429C
8869AF
B7A5CE
E3DAEB
F3F0F8

Requirements
Must have
• Logo & details listed above
Should not have
• No red or orange

```html
<!DOCTYPE html>
<html lang="en">
<head>
<meta charset="utf-8">
<title>Walk Beside The River – Business Card</title>
<link rel="stylesheet" href="https://fonts.googleapis.com/css2?family=Open+Sans:wght@400;600;700&display=swap">
<style>
  :root {
    --backdrop: #2b2b2e;
    --card-black: #1f1f23;
    --sun-yellow: #f2e52c;
    --sun-gold: #e9c22a;
    --river-purple: #6b429c;
    --text-light: #f3f0f8;
  }
  html, body {
    margin: 0;
    padding: 0;
    width: 1200px;
    height: 780px;
    overflow: hidden;
    background: var(--backdrop);
    font-family: "Open Sans", Arial, sans-serif;
  }
  .canvas {
    position: relative;
    width: 1200px;
    height: 780px;
  }
  .card {
    position: absolute;
    top: 225px;
    width: 540px;
    height: 330px;
    border-radius: 22px;
    overflow: hidden;
  }
  .card-front {
    left: 45px;
    background: var(--card-black);
    box-shadow: inset 0 0 0 3px var(--sun-yellow);
  }
  .card-back {
    left: 615px;
  }
  .front-shapes {
    position: absolute;
    inset: 0;
  }
  .brand {
    position: absolute;
    left: 40px;
    top: 26px;
    display: flex;
    align-items: center;
    gap: 10px;
  }
  .brand-dot {
    width: 22px;
    height: 22px;
    border-radius: 50%;
    background: var(--river-purple);
  }
  .brand-name {
    font-weight: 600;
    font-size: 16px;
    color: var(--text-light);
    letter-spacing: 0.5px;
  }
  .person {
    position: absolute;
    left: 40px;
    top: 72px;
  }
  .person-name {
    margin: 0;
    font-size: 30px;
    font-weight: 700;
    line-height: 1.1;
    letter-spacing: -0.3px;
  }
  .person-first { color: var(--sun-yellow); }
  .person-last { color: var(--river-purple); }
  .person-role {
    margin: 2px 0 0;
    font-size: 15px;
    color: var(--text-light);
  }
  .contacts {
    position: absolute;
    left: 30px;
    top: 150px;
    margin: 0;
    padding: 0;
    list-style: none;
    font-size: 14px;
    color: var(--text-light);
    line-height: 1.55;
  }
  .contacts li {
    display: flex;
    align-items: center;
    gap: 8px;
  }
  .contact-icon {
    width: 13px;
    height: 13px;
    flex: none;
  }
  .service {
    position: absolute;
    right: 40px;
    top: 222px;
    margin: 0;
    font-size: 15px;
    line-height: 1.4;
    color: var(--text-light);
  }
  .back-fill {
    width: 100%;
    height: 100%;
    background: linear-gradient(120deg, var(--sun-yellow) 0%, var(--sun-yellow) 45%, var(--sun-gold) 70%, #f7ec6a 100%);
  }
</style>
</head>
<body>
<main class="canvas">

  <section class="card card-front" aria-label="Business card front">
    <svg class="front-shapes" viewBox="0 0 540 330" aria-hidden="true">
      <rect x="26" y="74" width="6" height="34" fill="var(--sun-yellow)"/>
      <rect x="0" y="282" width="300" height="4" fill="var(--sun-yellow)"/>
      <rect x="0" y="290" width="300" height="40" fill="var(--river-purple)"/>
      <polygon points="300,282 312,282 330,330 300,330" fill="var(--card-black)"/>
      <polygon points="312,282 540,282 540,330 330,330" fill="var(--sun-yellow)"/>
    </svg>

    <div class="brand">
      <span class="brand-dot"></span>
      <span class="brand-name">Walk Beside The River</span>
    </div>

    <div class="person">
      <h1 class="person-name"><span class="person-first">Ilona</span> <span class="person-last">Varenne</span></h1>
      <p class="person-role">CEO/Director</p>
    </div>

    <ul class="contacts">
      <li>
        <svg class="contact-icon" viewBox="0 0 16 16" aria-hidden="true"><path d="M3 1h3l1.5 4-2 1.3a9 9 0 0 0 4.2 4.2L11 8.5l4 1.5v3a2 2 0 0 1-2 2A12 12 0 0 1 1 3a2 2 0 0 1 2-2z" fill="var(--sun-yellow)"/></svg>
        0481 637 092
      </li>
      <li>
        <svg class="contact-icon" viewBox="0 0 16 16" aria-hidden="true"><rect x="1" y="3" width="14" height="10" rx="1.5" fill="var(--sun-yellow)"/><path d="M1.5 4 8 9l6.5-5" stroke="var(--card-black)" stroke-width="1.4" fill="none"/></svg>
        walkbesidetheriver@mailcove.com.au
      </li>
      <li>
        <svg class="contact-icon" viewBox="0 0 16 16" aria-hidden="true"><path d="M8 1a5 5 0 0 1 5 5c0 4-5 9-5 9S3 10 3 6a5 5 0 0 1 5-5z" fill="var(--sun-yellow)"/><circle cx="8" cy="6" r="2" fill="var(--card-black)"/></svg>
        PO Box 926 Kelvale QLD 4571
      </li>
    </ul>

    <p class="service">Mental Health Support<br>Rosalind Tavener</p>
  </section>

  <section class="card card-back" aria-label="Business card back">
    <div class="back-fill" role="img" aria-label="Yellow card back with a repeating star pattern fading to a light shimmer"></div>
  </section>

</main>
</body>
</html>
```